Modern Business Card for Larkwell 2018

Our company assumes the best about people. We are creating an online community of entrepreneurs and business leaders who struggle with marketing their business online.

This business card should POP! We recently got a new logo and are launching a new website next month, so our business cards should make a statement that feels:
-Fresh
-Smart
-Trustworthy
-Fun

Target Market(s)

small business owners, entrepreneurs

Industry/Entity Type

Digital Marketing

Contact Information for Business Card

Dimensions: 3.5" x 2"

Font styles to use
Sans Serif

Colors
f37122
ffffff

Requirements
Must have
• We need a business card with a modern, bold design. We will use one side of the card as a lead-generation offer, so text on one side will need to fit up to 140 characters. The business card should stick to our core colors (orange, black, and white).
Nice to have
• We think a vertical "portrait" design could be interesting.
Should not have
• Should not look like a traditional business card. The round icon should stand out from a distance.

```html
<!DOCTYPE html>
<html lang="en">
<head>
<meta charset="utf-8">
<title>Larkwell Business Card</title>
<link rel="stylesheet" href="https://fonts.googleapis.com/css2?family=Oswald:wght@500&family=Work+Sans:wght@400;500;800&family=Roboto:wght@300;400&display=swap">
<style>
  :root {
    --backdrop: #2b2b2c;
    --card: #1b1b1c;
    --card-edge: #262627;
    --silver: #d9d9da;
    --grey-text: #a9a9ab;
    --gloss: #5a5a5d;
    --gloss-light: #6e6e71;
    --gloss-shadow: #0b0b0c;
    --rule: #4a4a4c;
  }
  * { box-sizing: border-box; margin: 0; padding: 0; }
  html, body { width: 1200px; height: 900px; overflow: hidden; }
  body {
    background: var(--backdrop);
    display: flex;
    flex-direction: column;
    align-items: center;
    justify-content: center;
    gap: 28px;
  }
  .card {
    width: 700px;
    height: 400px;
    background: var(--card);
    border: 1px solid var(--card-edge);
    position: relative;
  }
  /* front */
  .card--front {
    display: flex;
    flex-direction: column;
    align-items: center;
    padding-top: 70px;
  }
  .brand-dot {
    width: 64px; height: 64px;
    border-radius: 50%;
    background: var(--silver);
    margin-bottom: 18px;
  }
  .brand-name {
    font-family: "Work Sans", sans-serif;
    font-weight: 800;
    font-size: 68px;
    letter-spacing: 2px;
    color: var(--silver);
    line-height: 1;
  }
  .offer {
    margin-top: 26px;
    font-family: "Roboto", sans-serif;
    font-weight: 300;
    font-size: 14px;
    line-height: 1.45;
    text-align: center;
    color: var(--grey-text);
  }
  .offer-rule {
    width: 520px;
    height: 1px;
    background: var(--rule);
    margin: 12px 0 10px;
  }
  .tagline {
    font-family: "Roboto", sans-serif;
    font-size: 17px;
    letter-spacing: 0.5px;
    color: var(--grey-text);
  }
  /* back */
  .card--back { font-family: "Work Sans", sans-serif; }
  .identity {
    position: absolute;
    right: 372px; top: 136px;
    text-align: right;
    white-space: nowrap;
  }
  .person-name {
    font-family: "Oswald", sans-serif;
    font-weight: 500;
    font-size: 34px;
    line-height: 1.15;
    letter-spacing: 2px;
    color: var(--gloss);
    text-shadow: 0 -1px 0 var(--gloss-shadow);
  }
  .person-role {
    font-size: 17px;
    color: var(--gloss);
    text-shadow: 0 -1px 0 var(--gloss-shadow);
  }
  .divider {
    position: absolute;
    left: 350px; top: 140px;
    width: 1px; height: 80px;
    background: var(--rule);
  }
  .contact-list {
    position: absolute;
    left: 380px; top: 138px;
    list-style: none;
  }
  .contact-item {
    display: flex;
    align-items: center;
    gap: 10px;
    font-size: 19px;
    color: var(--silver);
    line-height: 1.4;
  }
  .contact-item svg { width: 13px; height: 13px; fill: none; stroke: var(--grey-text); stroke-width: 2; }
  .address {
    position: absolute;
    left: 70px; bottom: 56px;
    font-size: 18px;
    color: var(--gloss-light);
    text-shadow: 0 -1px 0 var(--gloss-shadow);
    letter-spacing: 0.5px;
    white-space: nowrap;
  }
</style>
</head>
<body>
  <section class="card card--front">
    <div class="brand-dot"></div>
    <h1 class="brand-name">LARKWELL</h1>
    <p class="offer">Get your free Larkwell<br>Starter Package and our marketing guide today at</p>
    <div class="offer-rule"></div>
    <p class="tagline">REACH MORE PEOPLE. MAKE MORE MONEY. CREATE MORE IMPACT.</p>
  </section>

  <section class="card card--back">
    <div class="identity">
      <h2 class="person-name">DANA WHITMORE</h2>
      <p class="person-role">Story Marketing Coach</p>
    </div>
    <div class="divider"></div>
    <ul class="contact-list">
      <li class="contact-item">
        <svg viewBox="0 0 16 16"><path d="M4 2 L6 5 L5 7 Q7 10 9 11 L11 10 L14 12 L13 14 Q6 14 2 4 Z"/></svg>
        (555) 214-3870
      </li>
      <li class="contact-item">
        <svg viewBox="0 0 16 16"><rect x="2" y="4" width="12" height="8"/><path d="M2 4 L8 9 L14 4"/></svg>
        Dana@larkwellnow.com
      </li>
      <li class="contact-item">
        <svg viewBox="0 0 16 16"><circle cx="8" cy="8" r="6"/><path d="M2 8 H14 M8 2 Q4 8 8 14 M8 2 Q12 8 8 14"/></svg>
        www.larkwellnow.com
      </li>
    </ul>
    <p class="address">QX2040 , 18/6N. Marlowe Row Eastfield city, Northland</p>
  </section>
</body>
</html>
```